Popup Nightclub Grand Opening Flyer

We need to design a flyer for the grand opening of an upscale, exclusive nightclub called "Lantern". The design needs to be chic and exclusive. The background should be black and the text should primarily be white. We like minimalist designs.

Here is the text for the flyer
-
Velvetroll Atlanta Presents

Lantern (LOGO)

A Popup Nightclub Experience
For one night Only

Friday, October 18, 2013
Party begins at 9PM

INVITE ONLY

See invitation for location details
(Velvetroll Atlanta logo)

-
Examples we like

http://cdn4-x.pressfolio-example.com/sites/default/files/styles/image_content_width/hash/3b/fd/2468013579_4421_flyer.jpg?itok=K9rtQw2z

http://files.hubspace-example.net/files/8Hqq-Tr72WWE3kaRbTmcxP5QZK2F396J8nbRw4CKMHfdX2Y7qSEF-MqjxDoNrLY3QCyQJD7npjGaRq3k-Mhx6hqf3MDSWf8r3/2zenSaturdays.jpg

http://morvex-example.com/wp-content/uploads/siteskin/widgetkit/gallery/2zen/2zen-gen_qstay4-01.jpg

Hi All, one thing that we are seeing that we don't like is on over emphasis on the phrase "a popup nightclub experience" please don't make this the largest thing on the flyer

Target Market(s)

Target market is 25-35 year olds who are affluent (rich) and like luxury brands

Requirements
Must have
• Dark Background
Nice to have
• Velvetroll Logo on the bottom
Modern text that isn't curvy
Should not have
• Curved text

```html
<!DOCTYPE html>
<html lang="en">
<head>
<meta charset="utf-8">
<title>Lantern Nightclub – Popup Opening Flyer</title>
<link rel="stylesheet" href="https://fonts.googleapis.com/css2?family=Nunito:wght@300;900&family=Oswald:wght@400;500&display=swap">
<style>
  :root {
    --ink: #000000;
    --white: #ffffff;
    --silver: #cfcfcf;
    --mark-grey: #bdbdbd;
    --violet: #8447f0;
    --smoke: rgba(150, 170, 165, 0.28);
  }
  html, body {
    margin: 0;
    padding: 0;
    background: var(--ink);
    overflow: hidden;
  }
  .flyer {
    position: relative;
    width: 928px;
    height: 1200px;
    background: var(--ink);
    overflow: hidden;
    font-family: "Nunito", sans-serif;
    color: var(--white);
  }
  .smoke {
    position: absolute;
    inset: 0;
    background:
      radial-gradient(ellipse 38% 22% at 40% 62%, var(--smoke), transparent 70%),
      radial-gradient(ellipse 30% 18% at 70% 40%, rgba(150,170,165,0.18), transparent 70%),
      radial-gradient(ellipse 40% 20% at 55% 78%, rgba(150,170,165,0.14), transparent 70%);
  }
  .presenter {
    position: absolute;
    top: 8px;
    left: 0;
    width: 100%;
    text-align: center;
    font-weight: 900;
    font-size: 54px;
    letter-spacing: 0.5px;
    margin: 0;
  }
  .brand-dot {
    position: absolute;
    left: 359px;
    top: 90px;
    width: 210px;
    height: 210px;
    border-radius: 50%;
    background: var(--mark-grey);
  }
  .brand-name {
    position: absolute;
    top: 410px;
    left: 0;
    width: 100%;
    text-align: center;
    font-weight: 300;
    color: var(--white);
    margin: 0;
  }
  .brand-name .word {
    display: block;
    font-size: 132px;
    letter-spacing: 18px;
    line-height: 1;
    padding-left: 18px;
  }
  .brand-name .tag {
    display: block;
    font-size: 62px;
    letter-spacing: 9px;
    line-height: 1;
    margin-top: 30px;
    padding-left: 9px;
  }
  .start-time {
    position: absolute;
    top: 700px;
    left: 40px;
    width: 860px;
    text-align: center;
    font-weight: 900;
    font-size: 66px;
    color: var(--violet);
    transform: rotate(13deg);
    margin: 0;
    white-space: nowrap;
  }
  .date {
    position: absolute;
    top: 905px;
    left: 0;
    width: 100%;
    text-align: center;
    font-weight: 900;
    font-size: 62px;
    letter-spacing: 1px;
    margin: 0;
  }
  .pitch {
    position: absolute;
    top: 1002px;
    left: 0;
    width: 100%;
    text-align: center;
    font-weight: 900;
    font-size: 44px;
    line-height: 60px;
    color: var(--silver);
    margin: 0;
  }
  .access {
    position: absolute;
    left: 16px;
    top: 1122px;
    font-family: "Oswald", sans-serif;
    font-weight: 500;
    font-size: 54px;
    color: var(--silver);
    margin: 0;
    letter-spacing: -0.5px;
  }
  .location-note {
    position: absolute;
    left: 255px;
    top: 1140px;
    font-family: "Oswald", sans-serif;
    font-weight: 400;
    font-size: 33px;
    color: var(--silver);
    margin: 0;
  }
  .host-mark {
    position: absolute;
    right: 18px;
    top: 1106px;
    font-weight: 900;
    font-size: 26px;
    color: var(--white);
    margin: 0;
  }
</style>
</head>
<body>
  <main class="flyer">
    <div class="smoke" role="img" aria-label="Soft wisps of grey smoke drifting across a black background"></div>

    <h2 class="presenter">Velvetroll Atlanta Presents</h2>

    <div class="brand-dot" aria-hidden="true"></div>
    <h1 class="brand-name">
      <span class="word">LANTERN</span>
      <span class="tag">NIGHTCLUB</span>
    </h1>

    <p class="start-time">PARTY BEGINS @ 9 PM</p>

    <p class="date">FRIDAY, OCTOBER 18, 2013</p>

    <p class="pitch">A Popup Nightclub experience<br>for one night only</p>

    <p class="access">invite only</p>
    <p class="location-note">see invitation for LOCATION DETAILS</p>

    <p class="host-mark">Velvetroll</p>
  </main>
</body>
</html>
```